Yoga/movement guide/teacher for adult yoga practice and kid yoga

What is the positioning or mission statement of your company? to guide individuals in a yoga-based safe and sustainable movement practice applicable to all ages and body types. Currently my focus is working with children in daycare and school settings, but my goal is to expand into private yoga practice for adults, and potentially as part of rented space in studios. I hope to find a way to work with children AND adults (so would love for logo to be appealing to both), but current focus is with children based on need and demand in the community. yoga for children also compliments my backround as a pediatrician/neonatologist, and I greatly miss interacting with children. I also want to emphasize a yoga/movement practice that is focused more on what one feels internally through movement. NOT what one looks like asthetically. I believe in removing all mirrors from yoga/movement practice. It should be an experience of movement/poses/yoga through appropriate cueing and education. It is not about the details of how far the knee should bend, or how high the leg should be. Focusing on foudation first, core, then core engagement and ultimately expression of poses/movements. A focus on strength, stability and mobility, not just flexibility, which is the common perception/association with yoga. I also want individuals to learn to be an advocate of their own health. Through guidance, I hope for individuals to connect with their body so they know themselves so well to be able to advocate for themselves in the modern healthcare world. This internal experience and connection is so essential in a world where modern medicine has become a business and it is all about making a dollar. the connection with patients is lost, and individuals need to learn to empower themselves and through their new found voice to be able to articulate what is wrong.<br/>Does your company have a tagline or slogan that should be included with the logo? "Move With Inner Light"<br/>What do you hope your company can be known for? Accessible yoga for a sustained practice. A guided movement practice where one gains information and knowledge of oneself through a mind/body connection. For one feel good physically with a new awaraness of their internal radiance that exists in all beings. Physical rejuvenation egnites a light and increases energy to flow through the physical body, which ultimately tranlates into works of kindness for others and out in the world. <br/>What color palettes might you prefer? why? love the colors currently chosen<br/>Where will the logo be primarily used? initially business cards, but hopefully future websites, t-shirts, and potentially local magazine adds. Also starting with a small couple of banners for community events in the area. I currently practice as a nomad out of my car :)<br/>Are there any elements you would prefer to see in the logo? Movement. A modern depiction of a human body/figure practicing movement. Hoping to avoid a stereotypical yoga pose per say, just because I want to people to think of it more of a movement practice with yoga roots. Modern yoga. There are elements of breathing and connecting with oneself through the flow of breath and movement, but I do not focus on the meditative/cerebral aspect of the yoga practice. What I teach is almost reaching a meditative state through movement. I personally don't practice, nor resonate with just seated meditation. just not my thing :)<br/>In your opinion, what defines a well-designed logo? curiosity. enough info for individuals to think they know what it means, but want to know more. invokes curiosity, but not too abstract. Reproducible. not too complicated. I want also to invoke a community feel, so a design that appeals to all people within a community. <br/>What is your preference in reference to icons, typography, spokespeople (characters), etc.? modern design. I love the idea of a logo for my purposes, to invoke a sense of movement from within. So not too static. <br/>What words or icons must be included in the logo? movement with yoga roots. <br/>What logos do you like and why? A representation, but not exact. I think some ambiguity is intriguing for others, and also memorable. I want it to be an artistic representation of movement/yoga<br/>What logos do you dislike and why? too busy, too loud. <br/>In your opinion, what is the primary purpose for a logo? association<br/>Who is the primary target audience? (who is most likely to use your services/product?) Children and their parents, but ultimately to expand into teaching adults. I even have aspirations of prenatal and post-natal yoga. Potentially incorporating infants. <br/>Who currently uses your product the most? n/a (working in schools/daycare currently. It is currently all volunteer)<br/>Are you pleased with the range of people your company serves? n/a<br/>Are you looking to expand, modify, or completely change your target audience? or will it remain the same? yes! expand into an adult audience. <br/>How do you plan to focus on your target audience? currently by working through schools and daycares. hopefully ultimately through after school care programs and then offering kid yoga in an existing yoga studio (working on this with Q Studio in Ridgeland, currently)<br/>What are your main forms of advertising? word of mouth, schools, daycares. Happy kids talking to their parents about the yoga class they took and happy teachers :)<br/>How do most customers find out about your company?<br/>Which gender are you targeting? All genders! However, with kid yoga, often the maternal individual in the child's life is more involved with decision making as far as extracurricular activities

Target Market(s)

individuals and families interested in wellness and feeling great

Contact Information for Business Card

Dana Whitford
Yoga Instructor
RYT-200, RCYT

certified yoga teacher for adults and children

Colors

Designer to choose colors to be used in the design.

Requirements
Must have
• "Move With Inner Light"
Nice to have
• logo with same colors

```html
<!DOCTYPE html>
<html lang="en">
<head>
<meta charset="utf-8">
<title>Glowmotion Studio – Business Card</title>
<link rel="stylesheet" href="https://fonts.googleapis.com/css2?family=Arimo:wght@400;700&display=swap">
<style>
  :root {
    --page-bg: #e9e7e5;
    --card-bg: #f7f5f3;
    --teal: #5fc8d0;
    --sun-yellow: #f6d63a;
    --social-blue: #2a5d9c;
    --white: #ffffff;
  }
  html, body {
    margin: 0;
    width: 1200px;
    height: 900px;
    overflow: hidden;
    background: var(--page-bg);
    font-family: "Arimo", Arial, sans-serif;
  }
  .business-card {
    position: absolute;
    left: 150px;
    top: 180px;
    width: 900px;
    height: 540px;
    background: var(--card-bg);
    overflow: hidden;
    box-shadow: 0 6px 24px rgba(0,0,0,0.12);
  }
  .contact-panel {
    position: absolute;
    left: 0;
    top: 0;
    width: 900px;
    height: 540px;
  }
  .person {
    position: absolute;
    left: 52px;
    top: 104px;
    color: var(--white);
  }
  .person-name {
    margin: 0;
    font-size: 31px;
    font-weight: 700;
    letter-spacing: 0.3px;
    text-transform: uppercase;
    line-height: 36px;
  }
  .person-role {
    margin: 0;
    font-size: 23px;
    font-weight: 400;
    line-height: 28px;
  }
  .contact-list {
    position: absolute;
    left: 54px;
    top: 284px;
    margin: 0;
    padding: 0;
    list-style: none;
    color: var(--white);
    font-size: 23px;
  }
  .contact-list li {
    display: flex;
    align-items: center;
    height: 33px;
  }
  .contact-icon {
    width: 18px;
    height: 18px;
    margin-right: 10px;
    fill: var(--white);
  }
  .address {
    position: absolute;
    left: 54px;
    top: 412px;
    margin: 0;
    color: var(--white);
    font-size: 23px;
    font-style: normal;
    line-height: 33px;
  }
  .social-links {
    position: absolute;
    left: 645px;
    top: 70px;
    display: flex;
    gap: 4px;
  }
  .social-dot {
    width: 44px;
    height: 44px;
    border-radius: 50%;
    background: var(--social-blue);
  }
  .brand {
    position: absolute;
    left: 560px;
    top: 290px;
    width: 320px;
  }
  .brand-lockup {
    display: flex;
    align-items: center;
    gap: 12px;
  }
  .brand-dot {
    width: 56px;
    height: 56px;
    border-radius: 50%;
    background: var(--sun-yellow);
    flex: none;
  }
  .brand-name {
    margin: 0;
    font-size: 30px;
    font-weight: 400;
    color: var(--teal);
    line-height: 1.05;
  }
  .brand-tagline {
    margin: 14px 0 0 68px;
    font-size: 11px;
    letter-spacing: 2px;
    color: var(--teal);
    text-transform: uppercase;
  }
</style>
</head>
<body>
  <main class="business-card">
    <svg class="contact-panel" viewBox="0 0 900 540" aria-hidden="true">
      <path d="M0,0 H476 C445,40 345,110 340,200 C336,260 390,290 450,330 C510,370 520,420 490,470 C468,510 445,540 420,540 H0 Z"
            fill="var(--teal)"/>
      <path d="M476,0 C445,40 345,110 340,200 C336,260 390,290 450,330 C510,370 520,420 490,470 C468,510 445,540 420,540"
            fill="none" stroke="var(--sun-yellow)" stroke-width="4"/>
    </svg>

    <header class="person">
      <h1 class="person-name">Dana Whitford</h1>
      <p class="person-role">Yoga Instructor</p>
    </header>

    <ul class="contact-list">
      <li>
        <svg class="contact-icon" viewBox="0 0 24 24"><path d="M6.6 10.8a15.1 15.1 0 0 0 6.6 6.6l2.2-2.2a1 1 0 0 1 1-.25 11.4 11.4 0 0 0 3.6.57 1 1 0 0 1 1 1V20a1 1 0 0 1-1 1A17 17 0 0 1 3 4a1 1 0 0 1 1-1h3.5a1 1 0 0 1 1 1c0 1.25.2 2.45.57 3.57a1 1 0 0 1-.25 1z"/></svg>
        044-555 010 234
      </li>
      <li>
        <svg class="contact-icon" viewBox="0 0 24 24"><path d="M2 5h20v14H2z M3 6l9 7 9-7" fill="var(--white)" stroke="var(--teal)" stroke-width="1.5"/></svg>
        hello@glowmotion.example
      </li>
      <li>
        <svg class="contact-icon" viewBox="0 0 24 24"><circle cx="12" cy="12" r="10"/><path d="M2 12h20M12 2c3 3 3 17 0 20M12 2c-3 3-3 17 0 20" fill="none" stroke="var(--teal)" stroke-width="1.4"/></svg>
        www.glowmotion.example
      </li>
    </ul>

    <address class="address">
      17 Meadow Lane, Suite 2<br>
      39157, Ridgeland
    </address>

    <nav class="social-links" aria-label="Social media">
      <span class="social-dot"></span>
      <span class="social-dot"></span>
      <span class="social-dot"></span>
      <span class="social-dot"></span>
    </nav>

    <section class="brand">
      <div class="brand-lockup">
        <span class="brand-dot"></span>
        <p class="brand-name">Glowmotion Studio</p>
      </div>
      <p class="brand-tagline">Move With Inner Light</p>
    </section>
  </main>
</body>
</html>
```